Meridale Real Estate

We are looking for help with web design for a new company that is revolutionizing the real estate world on the listing side: by charing per hour for top level professional real estate services. We would like the concept to be simple, clean and easily understood.
Updates

We want this website to actually function, not just a static design.

Industry/Entity Type

Real Estate

```html
<!DOCTYPE html>
<html lang="en">
<head>
<meta charset="utf-8">
<title>Meridale Real Estate</title>
<link href="https://fonts.googleapis.com/css2?family=Arimo:wght@400;700&display=swap" rel="stylesheet">
<style>
:root{
  --ink:#3a3a3a;
  --muted:#8d8d8d;
  --brand:#c49a6c;
  --blue:#2b93d6;
  --blue-dark:#1f78b8;
  --band:rgba(38,38,38,.84);
  --panel:#e8e7e8;
  --rule:#d4d4d4;
  --dark-card:#2a2a2a;
  --white:#ffffff;
}
*{box-sizing:border-box;margin:0;padding:0}
html,body{width:1200px;height:1121px;overflow:hidden;background:var(--white)}
body{position:relative;font-family:"Arimo",Arial,sans-serif;color:var(--ink)}
a{text-decoration:none}
.abs{position:absolute}

/* header */
.site-header{position:absolute;left:0;top:0;width:1200px;height:88px;background:var(--white)}
.brand{left:232px;top:52px;display:flex;align-items:center;gap:8px;z-index:3}
.brand-dot{width:14px;height:14px;border-radius:50%;border:2px solid var(--brand)}
.brand-name{font-size:15px;font-weight:700;letter-spacing:1.5px;color:var(--brand);text-transform:uppercase}
.header-divider{left:483px;top:24px;width:1px;height:46px;background:var(--rule)}
.main-nav{left:503px;top:42px;font-size:9px;color:var(--muted)}
.main-nav a,.account a{color:inherit}
.account{left:936px;top:42px;font-size:9px;color:var(--muted)}
.account .login{color:var(--blue)}

/* hero */
.hero{left:0;top:88px;width:1200px;height:373px;
  background:
    linear-gradient(90deg,rgba(90,80,60,.55) 0%,rgba(0,0,0,0) 9%,rgba(0,0,0,0) 100%),
    linear-gradient(180deg,#55504a 0%,#8a5a48 12%,#b4aea6 24%,#ecebe8 38%,#e6e5e2 62%,#d8d6d2 82%,#9a978f 100%)}
.search-band{left:0;top:239px;width:1200px;height:118px;background:var(--band)}
.search-title{left:416px;top:249px;font-size:20px;color:#d0d0d0}
.search-input{left:416px;top:283px;width:293px;height:25px;background:var(--white);font-size:10px;color:#9a9a9a;padding:7px 6px}
.search-btn{left:732px;top:283px;width:77px;height:25px;background:linear-gradient(#3aa3e3,var(--blue-dark));color:var(--white);font-size:10px;font-weight:700;text-align:center;line-height:25px}
.select{top:316px;width:92px;height:27px;background:var(--white);font-size:9px;color:#777;padding:9px 6px}
.select::after{content:"";position:absolute;right:8px;top:11px;border:5px solid transparent;border-top-color:#888}
.advanced{left:740px;top:325px;font-size:9px;color:#6fb8ea;text-decoration:underline}
.slide-arrow{top:402px;width:18px;height:28px}
.slide-caption{left:500px;top:405px;width:240px;text-align:center;font-size:10px;line-height:16px;color:var(--white);text-shadow:0 1px 2px rgba(0,0,0,.5)}

/* listings */
.listings{left:0;top:461px;width:1200px;height:343px;background:var(--panel)}
.tabs a{position:absolute;top:481px;font-size:9px;color:#666}
.tabs .active{color:var(--blue)}
.tabs-rule{left:227px;top:505px;width:766px;height:1px;background:var(--rule)}
.tab-pointer{left:262px;top:505px;border:9px solid transparent;border-top-color:var(--white);border-top-width:8px}
.feature-card{left:227px;top:527px;width:350px;height:216px;
  background:
    linear-gradient(90deg,rgba(0,0,0,0) 40%,rgba(150,95,45,.55) 75%,rgba(120,80,40,.3) 100%),
    linear-gradient(180deg,#3a3936 0%,#262726 55%,#2c3a2c 85%,#2a3a48 100%)}
.feature-card h2{position:absolute;left:56px;top:58px;font-size:15px;font-weight:400;color:var(--white)}
.feature-card p{position:absolute;left:56px;top:92px;width:260px;font-size:9px;line-height:13px;color:#ddd}
.btn-find{position:absolute;left:56px;top:144px;width:81px;height:26px;background:linear-gradient(#45aee8,var(--blue-dark));color:var(--white);font-size:11px;font-weight:700;text-align:center;line-height:26px}
.photo{width:182px;height:101px}
.info-card{left:811px;top:641px;width:182px;height:102px;background:var(--dark-card)}
.info-card h3{position:absolute;left:23px;top:18px;font-size:9px;font-weight:700;color:var(--white)}
.info-card .price{position:absolute;right:22px;top:16px;font-size:11px;font-weight:700;color:#3aa3e3}
.info-card p{position:absolute;left:23px;top:46px;width:140px;font-size:7.5px;line-height:11px;color:#cfcfcf}
.info-card a{position:absolute;left:23px;top:80px;font-size:6.5px;font-weight:700;color:var(--blue)}

/* app promo */
.phone{left:227px;top:832px;width:112px;height:179px;border-radius:14px;background:#111;padding:24px 8px 30px}
.tablet{left:325px;top:897px;width:51px;height:114px;border-radius:8px;background:#111;border:2px solid #fff;padding:14px 4px 18px}
.screen{width:100%;height:100%;background:linear-gradient(180deg,#f2f2f2 0%,#dcdcdc 20%,#3a3a3a 45%,#c9c2b8 65%,#7e7468 100%)}
.app-title{left:391px;top:838px;font-size:13.5px;line-height:19px;color:#7a7a7a;font-weight:400}
.app-text{left:391px;top:895px;font-size:8px;color:#888}
.store-btn{top:936px;width:102px;height:27px;border-radius:2px;padding:4px 8px;color:var(--white);line-height:1.15}
.store-btn small{display:block;font-size:6px}
.store-btn span{display:block;font-size:9px;font-weight:700}
.store-ios{left:391px;background:linear-gradient(#d6d6d6,#a9a9a9)}
.store-droid{left:504px;background:linear-gradient(#a7d24f,#7ab02a);color:#2d3a10}
.store-droid span{color:#fff}
.promo-divider{left:643px;top:829px;width:1px;height:191px;background:var(--rule)}
.accordion{left:703px;top:839px;width:166px}
.acc-item{position:relative;height:25.5px;border-bottom:1px solid #e6e6e6;font-size:8.5px;color:#8a8a8a;padding-top:7px}
.acc-item::after{content:"";position:absolute;right:0;top:9px;border:4px solid transparent;border-left:6px solid #c9c9c9}
.acc-item.open{border-bottom:none}
.acc-item.open::after{top:11px;border:4px solid transparent;border-top:5px solid #c9c9c9}
.acc-body{font-size:7px;line-height:11px;color:#b0b0b0;height:40px;padding-top:2px;border-bottom:1px solid #e6e6e6}

/* footer */
.footer-rule{left:227px;top:1051px;width:766px;height:1px;background:var(--rule)}
.copyright{left:233px;top:1082px;font-size:9px;font-weight:700;color:#444}
.social{top:1075px;width:21px;height:21px;background:#b9b9b9}
</style>
</head>
<body>

<header class="site-header">
  <div class="abs header-divider"></div>
  <nav class="abs main-nav"><a href="#">Find Property</a> &nbsp;|&nbsp; <a href="#">Lorem Ipsum</a> &nbsp;|&nbsp; <a href="#">Renter Resource</a></nav>
  <div class="abs account"><a href="#">Sign In</a> &nbsp;|&nbsp; <a href="#" class="login">Login</a></div>
</header>

<section class="abs hero" role="img" aria-label="Photo of a white two-storey house with a red tiled roof and striped awnings"></section>
<div class="abs brand"><span class="brand-dot"></span><span class="brand-name">Meridale Real Estate</span></div>

<div class="abs search-band"></div>
<div class="abs search-title">find your property..</div>
<div class="abs search-input">city, state or zip</div>
<a class="abs search-btn" href="#">SEARCH</a>
<div class="abs select" style="left:416px">Bedrooms</div>
<div class="abs select" style="left:516px">Bathrooms</div>
<div class="abs select" style="left:617px">Max-Min</div>
<a class="abs advanced" href="#">Advance Search</a>

<svg class="abs slide-arrow" style="left:491px" viewBox="0 0 18 28"><path d="M14 3 4 14l10 11" fill="none" stroke="#fff" stroke-width="3"/></svg>
<svg class="abs slide-arrow" style="left:718px" viewBox="0 0 18 28"><path d="M4 3l10 11-10 11" fill="none" stroke="#fff" stroke-width="3"/></svg>
<div class="abs slide-caption"><strong>Heading of the Property Location</strong><br>Lorem Ipsum is Simple Dummy Text</div>

<section class="abs listings"></section>
<nav class="tabs">
  <a href="#" class="active" style="left:253px">All Types</a>
  <a href="#" style="left:356px">Pet Friendly</a>
  <a href="#" style="left:476px">Luxury</a>
  <a href="#" style="left:585px">Lorem Ipsum</a>
</nav>
<div class="abs tabs-rule"></div>
<div class="abs tab-pointer"></div>

<article class="abs feature-card" role="img" aria-label="Modern house with pool at dusk">
  <h2>Find An Apartment For Rent Anywhere</h2>
  <p>Lorem Ipsum is simply dummy text of the printing and typesetting industry Lorem Ipsum is simply dummy text of the printing and typesetting industry</p>
  <a class="btn-find" href="#">Find Now !</a>
</article>

<div class="abs photo" role="img" aria-label="Living room with white sofa and glass table" style="left:605px;top:527px;background:linear-gradient(180deg,#a9a39a 0%,#6a5a4a 30%,#e8e4dc 55%,#c8c0b4 80%,#9a8c7c 100%)"></div>
<div class="abs photo" role="img" aria-label="Bright bedroom with sea view" style="left:811px;top:527px;background:linear-gradient(180deg,#e7e6e2 0%,#a8b8b4 22%,#5e6e62 40%,#e9e7e2 62%,#d7d1c8 100%)"></div>
<div class="abs photo" role="img" aria-label="Lounge with beige sofas" style="left:605px;top:641px;height:102px;background:linear-gradient(180deg,#c9c4bc 0%,#8a7e72 35%,#d9c8b0 60%,#b8a48a 80%,#e2ddd6 100%)"></div>

<article class="abs info-card">
  <h3>HEADING HERE</h3>
  <span class="price">$700.00</span>
  <p>Lorem Ipsum is simply dummy text of the printing and typesetting industry.</p>
  <a href="#">READ MORE</a>
</article>

<div class="abs phone" role="img" aria-label="Phone showing the mobile app"><div class="screen"></div></div>
<div class="abs tablet" role="img" aria-label="Small handset showing the mobile app"><div class="screen"></div></div>
<h2 class="abs app-title">Find an apartment on the<br>Handset/Tablet App or Droidline App</h2>
<p class="abs app-text">Lorem Ipsum is simply dummy text of the printing</p>
<a class="abs store-btn store-ios" href="#"><small>Available on</small><span>PocketOS Web App</span></a>
<a class="abs store-btn store-droid" href="#"><small>Available on</small><span>AppBazaar Market</span></a>
<div class="abs promo-divider"></div>

<div class="abs accordion">
  <div class="acc-item open">LOREM IPSUM</div>
  <div class="acc-body">Lorem Ipsum is simply dummy text of the printing and typesetting industry. Lorem Ipsum has</div>
  <div class="acc-item">LOREM IPSUM</div>
  <div class="acc-item">LOREM IPSUM</div>
  <div class="acc-item">LOREM IPSUM</div>
  <div class="acc-item">LOREM IPSUM</div>
</div>

<div class="abs footer-rule"></div>
<p class="abs copyright">Copyrights 2015 Meridale Real Estate. All Right Reserved</p>
<a class="abs social" href="#" aria-label="Social link" style="left:896px"></a>
<a class="abs social" href="#" aria-label="Social link" style="left:921px"></a>
<a class="abs social" href="#" aria-label="Social link" style="left:946px"></a>
<a class="abs social" href="#" aria-label="More" style="left:972px"><svg width="21" height="21" viewBox="0 0 21 21"><path d="M10.5 5v11M5 10.5h11" stroke="#fff" stroke-width="2.5"/></svg></a>

</body>
</html>
```